K SPIRES Business Card Design

Need a business card design for K Spires, we're a tower company - our main scope of work is to upgrade cellular sites: swap antennas, install new coax, fiber, replace mounts, etc. Mostly tower work.

would like to see a sharp business card design with our logo either on background or with tower image on the background - something describing our field not only in words but in images.

Target Market(s)

USA

Industry/Entity Type

Business

Contact Information for Business Card

Tarnek Obliva
Operations Manager
K Spires LLC

cell 555-318-2094
tarnek@k-spires-example.com

4185 Wexbridge Commerce Pkwy, Suite D
Norcross, GA, 30571

Requirements
Must have
• some tower related design
Nice to have
• some tower or cellular antennas on the background, if possible to compliment our logo...

```html
<!DOCTYPE html>
<html lang="en">
<head>
<meta charset="utf-8">
<title>K Spires Business Card</title>
<link rel="stylesheet" href="https://fonts.googleapis.com/css2?family=Lato:wght@400;700&family=Arimo:wght@400&display=swap">
<style>
  :root {
    --stage: #2b2c2e;
    --card-front: #f4f4f2;
    --card-back: #1f2021;
    --green: #3aa517;
    --blue: #1f1fc4;
    --logo-grey: #b9b9b9;
    --tower-tint: #d9d9d7;
  }
  * { margin: 0; padding: 0; box-sizing: border-box; }
  html, body {
    width: 1200px;
    height: 864px;
    overflow: hidden;
    background: var(--stage);
  }
  .canvas {
    position: relative;
    width: 1200px;
    height: 864px;
  }
  .card {
    position: absolute;
    left: 341px;
    width: 519px;
    height: 305px;
    overflow: hidden;
  }
  .card--front {
    top: 96px;
    background: var(--card-front);
  }
  .card--back {
    top: 454px;
    background: var(--card-back);
  }
  .tower-backdrop {
    position: absolute;
    left: 222px;
    top: 0;
    width: 80px;
    height: 305px;
    background: linear-gradient(180deg, rgba(217,217,215,0.35), var(--tower-tint));
    clip-path: polygon(42% 0, 58% 0, 100% 100%, 0 100%);
  }
  .holder {
    position: absolute;
    left: 46px;
    top: 44px;
    font-family: "Lato", sans-serif;
  }
  .holder__name {
    color: var(--green);
    font-weight: 700;
    font-size: 25px;
    line-height: 30px;
  }
  .holder__role {
    color: var(--blue);
    font-weight: 400;
    font-size: 15.5px;
    line-height: 18px;
  }
  .contact {
    position: absolute;
    left: 46px;
    top: 152px;
    font-family: "Arimo", sans-serif;
    font-size: 13px;
    line-height: 18px;
  }
  .contact__label { color: var(--green); }
  .contact__value { color: var(--blue); white-space: nowrap; }
  .brand {
    position: absolute;
    font-family: "Lato", sans-serif;
    font-weight: 400;
    white-space: nowrap;
  }
  .brand--front {
    right: 30px;
    top: 140px;
    font-size: 56px;
    line-height: 60px;
    color: var(--blue);
  }
  .brand--back {
    left: 0;
    right: 0;
    top: 118px;
    text-align: center;
    font-size: 64px;
    line-height: 70px;
    color: var(--logo-grey);
  }
</style>
</head>
<body>
  <main class="canvas">
    <section class="card card--front" aria-label="Business card front">
      <div class="tower-backdrop" role="img" aria-label="Faint lattice cell tower rising through the card"></div>
      <div class="holder">
        <p class="holder__name">Tarnek Obliva</p>
        <p class="holder__role">Operations Manager</p>
      </div>
      <dl class="contact">
        <dt class="contact__label">telephone</dt>
        <dd class="contact__value">555-318-2094</dd>
        <dt class="contact__label">email</dt>
        <dd class="contact__value">tarnek@k-spires-example.com</dd>
        <dt class="contact__label">address</dt>
        <dd class="contact__value">4185 Wexbridge Commerce Pkwy, Suite D</dd>
        <dd class="contact__value">Norcross, GA, 30571</dd>
      </dl>
      <p class="brand brand--front">K Spires</p>
    </section>

    <section class="card card--back" aria-label="Business card back">
      <p class="brand brand--back">K Spires</p>
    </section>
  </main>
</body>
</html>
```